Telecommunications/Power civil contractor needs business card design

Were a new telecommunications/power underground civil contractor that is looking for a new business card design. Our company colours are silver or grey and orange. Feel free to use the white background logo or the black background logo.

Target Market(s)

Local contractors, utility companies, private sector mining/energy companies, developers.

Industry/Entity Type

Telecommunications

Contact Information for Business Card

Each card will need the following info:
Persons name:
Title:
E-mail:
Phone number:
Shop Address:
Mailing Address:

Requirements
Must have
• Each card will need the following info:
• Persons name:
• Title:
• E-mail:
• Phone number:
• Shop Address:
• Mailing Address:

```html
<!DOCTYPE html>
<html lang="en">
<head>
<meta charset="utf-8">
<title>Tread Line Contracting Inc – Business Card</title>
<link href="https://fonts.googleapis.com/css2?family=PT+Sans:wght@400;700&family=Montserrat:wght@800&display=swap" rel="stylesheet">
<style>
  :root {
    --page-bg: #e9e6e3;
    --card-face: #f4f2f0;
    --brand-orange: #f15a24;
    --brand-grey: #5a5a5c;
    --text-light: #ffffff;
  }
  * { margin: 0; padding: 0; box-sizing: border-box; }
  html, body {
    width: 1200px;
    height: 900px;
    overflow: hidden;
    background: var(--page-bg);
    font-family: "PT Sans", Arial, sans-serif;
  }
  .canvas { position: relative; width: 1200px; height: 900px; }

  .card {
    position: absolute;
    width: 556px;
    height: 342px;
    background: var(--card-face);
    box-shadow: 0 6px 18px rgba(0,0,0,0.12);
    overflow: hidden;
  }
  .card--front { left: 238px; top: 62px; }
  .card--back  { left: 458px; top: 518px; width: 560px; }

  .card__band {
    position: absolute;
    left: 0; right: 0; bottom: 0;
    background: var(--brand-orange);
    color: var(--text-light);
  }
  .card--front .card__band { top: 185px; }
  .card--back .card__band  { top: 187px; }

  /* Brand lockup */
  .brand { position: absolute; display: flex; align-items: center; gap: 26px; }
  .card--front .brand { left: 115px; top: 43px; }
  .brand__mark {
    width: 102px; height: 102px;
    border: 4px solid var(--brand-grey);
    border-radius: 50%;
    flex: none;
  }
  .brand__name {
    font-family: "Montserrat", Arial, sans-serif;
    font-weight: 800;
    font-size: 19px;
    line-height: 1.15;
    letter-spacing: 1px;
    text-transform: uppercase;
    color: var(--brand-orange);
    white-space: nowrap;
  }
  .brand--faint {
    left: 115px; top: 45px;
    opacity: 0.3;
    transform: scaleX(-1);
    transform-origin: center;
  }

  /* Front details */
  .holder {
    position: absolute;
    left: 102px; top: 54px;
  }
  .holder__name {
    font-size: 19px;
    font-weight: 700;
    line-height: 24px;
  }
  .holder__title {
    font-size: 14px;
    line-height: 18px;
  }
  .contact-list {
    position: absolute;
    left: 284px; top: 62px;
    list-style: none;
    font-size: 16px;
    line-height: 20px;
  }
  .contact-list li { display: flex; align-items: center; gap: 14px; }
  .contact-list svg { width: 12px; height: 12px; fill: var(--text-light); flex: none; }

  /* Back addresses */
  .address {
    position: absolute;
    top: 48px;
    font-size: 16px;
    line-height: 20px;
  }
  .address__title { font-size: 18px; font-weight: 700; line-height: 22px; }
  .address--shop { right: 296px; text-align: right; }
  .address--mail { left: 291px; }
</style>
</head>
<body>
<main class="canvas">

  <section class="card card--front" aria-label="Business card front">
    <div class="brand">
      <span class="brand__mark" aria-hidden="true"></span>
      <span class="brand__name">Tread Line<br>Contracting Inc</span>
    </div>
    <div class="card__band">
      <div class="holder">
        <p class="holder__name">Marcus Hale</p>
        <p class="holder__title">Project Manager</p>
      </div>
      <ul class="contact-list">
        <li>
          <svg viewBox="0 0 24 24" aria-hidden="true"><path d="M6.6 10.8a15.1 15.1 0 0 0 6.6 6.6l2.2-2.2c.3-.3.7-.4 1-.2 1.1.4 2.3.6 3.6.6.6 0 1 .4 1 1V20c0 .6-.4 1-1 1A17 17 0 0 1 3 4c0-.6.4-1 1-1h3.5c.6 0 1 .4 1 1 0 1.3.2 2.5.6 3.6.1.3 0 .7-.2 1z"/></svg>
          <span>044-555 018 274</span>
        </li>
        <li>
          <svg viewBox="0 0 24 24" aria-hidden="true"><path d="M2 6h20v12H2z"/><path d="M2 6l10 7 10-7" fill="none" stroke="#f15a24" stroke-width="2"/></svg>
          <span>info@treadline.com</span>
        </li>
      </ul>
    </div>
  </section>

  <section class="card card--back" aria-label="Business card back">
    <div class="brand brand--faint" aria-hidden="true">
      <span class="brand__mark"></span>
      <span class="brand__name">Tread Line<br>Contracting Inc</span>
    </div>
    <div class="card__band">
      <div class="address address--shop">
        <p class="address__title">Shop Address</p>
        <p>12345, Address Goes Here</p>
        <p>Country Name, 123456.</p>
      </div>
      <div class="address address--mail">
        <p class="address__title">Mailing Address</p>
        <p>12345, Address Goes Here</p>
        <p>Country Name, 123456.</p>
      </div>
    </div>
  </section>

</main>
</body>
</html>
```